Unravelling Markets - Podcast Cover

Unravelling Markets is a weekly podcast that dispels some of the myths about conventional economic thinking and provides a new way of thinking about issues that are faced by the global economy. It's insightful, thought-provoking and, most importantly, fun. We are refreshing the look and sound of the podcast. I have attached a copy of the old amateur design (which I did!)

Target Market(s)

Male oriented, smart folk with an interest in politics and economics

Font styles to use
Sans Serif

Requirements
Must have
• Clearly visible title, even when reduced in size. Must be 3000 pixels by 3000 pixels.
Nice to have
• This podcast challenges the status quo. It should reflect that. Photos and names of the hosts. Actually, because th ephotos are so different, we'd be open to the idea of a caricature if you can do that within the price.

```html
<!DOCTYPE html>
<html lang="en">
<head>
<meta charset="utf-8">
<title>Unravelling Markets – Podcast Cover</title>
<link href="https://fonts.googleapis.com/css2?family=Exo+2:wght@400;700;800&display=swap" rel="stylesheet">
<style>
  :root {
    --page: #d8d8d8;
    --navy-dark: #1d2935;
    --navy-light: #2c4656;
    --red: #e0140f;
    --red-title: #d8261f;
    --white: #ffffff;
    --grid: #e7c9cf;
    --dot-dim: #8a949c;
  }
  html, body {
    margin: 0;
    width: 1200px;
    height: 1105px;
    overflow: hidden;
    background: var(--page);
  }
  .stage {
    position: relative;
    width: 1200px;
    height: 1105px;
  }
  .cover {
    position: absolute;
    left: 179px;
    top: 132px;
    width: 1406px;
    height: 1406px;
    transform: scale(0.598);
    transform-origin: 0 0;
    background: linear-gradient(135deg, var(--navy-dark) 0%, #24384a 55%, var(--navy-light) 100%);
    box-shadow: 0 20px 40px rgba(0,0,0,0.25);
    font-family: "Exo 2", sans-serif;
    color: var(--white);
    overflow: hidden;
  }
  .chart {
    position: absolute;
    inset: 0;
  }
  .title-mark {
    position: absolute;
    left: 170px;
    top: 180px;
    width: 110px;
    height: 110px;
    background: var(--red-title);
  }
  .title {
    position: absolute;
    left: 330px;
    top: 95px;
    margin: 0;
    font-weight: 800;
    font-size: 122px;
    line-height: 132px;
    letter-spacing: 1px;
  }
  .title .line { display: block; }
  .title .line-accent { color: var(--red-title); font-size: 150px; line-height: 140px; }
  .host-name {
    position: absolute;
    margin: 0;
    font-size: 44px;
    font-weight: 400;
    letter-spacing: 0.5px;
    line-height: 1;
    padding: 0 16px;
    background: #23323f;
    white-space: nowrap;
  }
  .host-name strong { font-weight: 700; }
  .host-name.is-guest { left: 173px; top: 676px; }
  .host-name.is-host { left: 705px; top: 410px; background: #243544; }
  .host-role {
    position: absolute;
    margin: 0;
    font-size: 32px;
    line-height: 34px;
    font-weight: 400;
    letter-spacing: 0.5px;
  }
  .host-role.is-guest { left: 374px; top: 1212px; }
  .host-role.is-host { left: 872px; top: 896px; }
  .dots { display: flex; gap: 7px; margin-top: 8px; }
  .dots span { width: 11px; height: 11px; border-radius: 50%; background: var(--white); }
  .dots span:nth-child(2) { opacity: 0.8; }
  .dots span:nth-child(3) { background: var(--dot-dim); }
</style>
</head>
<body>
<div class="stage">
  <div class="cover">
    <svg class="chart" viewBox="0 0 1406 1406" width="1406" height="1406">
      <defs>
        <linearGradient id="photo-guest" x1="0" y1="0" x2="0" y2="1">
          <stop offset="0" stop-color="#3a3636"/>
          <stop offset="0.55" stop-color="#8a7f78"/>
          <stop offset="1" stop-color="#e6e3de"/>
        </linearGradient>
        <linearGradient id="photo-host" x1="0" y1="0" x2="0" y2="1">
          <stop offset="0" stop-color="#e4e5e8"/>
          <stop offset="0.5" stop-color="#c9a08c"/>
          <stop offset="1" stop-color="#2d8fa8"/>
        </linearGradient>
      </defs>
      <g class="grid" stroke="var(--grid)" stroke-width="1.6" fill="none">
        <line x1="105" y1="389" x2="1305" y2="389"/>
        <line x1="105" y1="543" x2="1305" y2="543"/>
        <line x1="105" y1="697" x2="1305" y2="697"/>
        <line x1="105" y1="851" x2="1305" y2="851"/>
        <line x1="105" y1="1005" x2="1305" y2="1005"/>
        <line x1="105" y1="1159" x2="1305" y2="1159"/>
        <line x1="339" y1="389" x2="339" y2="1314"/>
        <line x1="580" y1="389" x2="580" y2="1314"/>
        <line x1="822" y1="389" x2="822" y2="1314"/>
        <line x1="1063" y1="389" x2="1063" y2="1314"/>
        <line x1="1305" y1="389" x2="1305" y2="1314"/>
      </g>
      <g class="axes" fill="var(--red)">
        <rect x="82" y="395" width="22" height="930"/>
        <rect x="82" y="1303" width="1200" height="22"/>
        <polygon points="93,319 45,401 141,401"/>
        <polygon points="1362,1314 1280,1266 1280,1362"/>
      </g>
      <g class="trend" fill="none" stroke="var(--white)" stroke-width="20" stroke-linejoin="miter">
        <polyline points="105,1229 225,1124"/>
        <polyline points="512,999 615,994 730,844"/>
        <polyline points="990,744 1030,744 1180,539"/>
      </g>
      <polygon fill="var(--white)" points="1212,491 1125,537 1203,585"/>
      <circle cx="340" cy="1004" r="170" fill="url(#photo-guest)" stroke="var(--white)" stroke-width="9" role="img" aria-label="Portrait photo of guest Martin Hale"/>
      <circle cx="822" cy="694" r="172" fill="url(#photo-host)" stroke="var(--white)" stroke-width="9" role="img" aria-label="Portrait photo of podcast host Gary Lowell"/>
    </svg>

    <div class="title-mark"></div>
    <h1 class="title">
      <span class="line">UNRAVELLING</span>
      <span class="line line-accent">MARKETS</span>
    </h1>

    <p class="host-name is-guest"><strong>MARTIN</strong> HALE</p>
    <p class="host-name is-host"><strong>GARY</strong> LOWELL</p>

    <div class="host-role is-guest">PROFESSOR<div class="dots"><span></span><span></span><span></span></div></div>
    <div class="host-role is-host">PODCAST<br>HOST<div class="dots"><span></span><span></span><span></span></div></div>
  </div>
</div>
</body>
</html>
```